Bright Harbor website redesign

We need a redesign for a website: mybrightharbor.example.

I already created a video going over what exactly is needed in the design.

See Video here: https://files.example.net/file/d/7xQpL2mR9vTz4KwB8nYcH3jDs6FgA1eU0/view?usp=sharing

SearchStar Slide shown in Video: https://slides.example.net/presentation/d/9KP_Rtnwq3XbzmLeYc7VhJ2GoUd4Fs_PaiTe6q1kQ5Wr/edit?usp=sharing

Holidays in India so we did not get enough design entries or quality.

Target Market(s)

Dentistry

Industry/Entity Type

Dentistry

Number of Pages Required

1 page

Colors
0094D4
00A9DD
6FCCEA
C7EBF8
E9F6FB
00AB8E
00BBA5
67D7C9
C6EFE9
E9F9F6

Requirements
Must have
• See 13 min video link in description - shows what to do.

```html
<!DOCTYPE html>
<html lang="en">
<head>
<meta charset="utf-8">
<title>Bright Harbor – Dental Care</title>
<link href="https://fonts.googleapis.com/css2?family=Prata&family=Poppins:wght@400;500;600&family=Lobster+Two:ital@1&display=swap" rel="stylesheet">
<style>
:root{
  --green:#6b9d6c;
  --green-soft:#7aa97b;
  --teal-dark:#2d6664;
  --teal-deep:#1f3f3e;
  --aqua:#5ec6c4;
  --mint:#eef4ee;
  --ink:#222;
  --muted:#555;
  --white:#fff;
}
*{box-sizing:border-box;margin:0;padding:0}
html,body{width:1200px;height:4491px;overflow:hidden;background:var(--white)}
body{font-family:"Poppins",sans-serif;color:var(--ink);position:relative}
.abs{position:absolute}
.serif{font-family:"Prata",serif}
.script{font-family:"Lobster Two",cursive;font-style:italic}
.btn{position:absolute;background:var(--aqua);color:var(--teal-deep);font-family:"Prata",serif;font-size:13px;display:flex;align-items:center;justify-content:center;border-radius:4px;text-transform:uppercase;letter-spacing:.5px;white-space:nowrap}

/* hero */
.hero{position:absolute;left:0;top:0;width:1200px;height:760px;background:linear-gradient(120deg,#2c5a5c 0%,#4d7f80 45%,#9fb6b5 75%,#6d8e8f 100%)}
.topbar{position:absolute;left:0;top:0;width:1200px;height:45px;background:rgba(20,50,50,.55);display:flex;justify-content:flex-end;align-items:center;gap:28px;padding-right:60px;color:#fff;font-size:12px}
.topbar .phone{display:flex;align-items:center;gap:10px;font-size:11px;line-height:1.2}
.topbar .phone b{font-family:"Prata",serif;font-size:14px;font-weight:400;letter-spacing:1px}
.brand{position:absolute;font-family:"Lobster Two",cursive;font-style:italic;color:var(--green-soft);font-size:30px;white-space:nowrap}
.nav{position:absolute;left:275px;top:75px;display:flex;gap:27px;color:#fff;font-size:12px}
.nav .active{color:var(--aqua)}
.hero-kicker{position:absolute;left:61px;top:218px;color:#fff;font-size:30px;line-height:36px}
.hero-title{position:absolute;left:61px;top:262px;font-family:"Prata",serif;font-weight:400;color:#fff;font-size:57px;line-height:66px;white-space:nowrap}
.hero-lead{position:absolute;left:61px;top:403px;color:#fff;font-size:12px}

/* team */
.eyebrow{font-family:"Lobster Two",cursive;font-style:italic;color:var(--green);font-size:28px}
.heading{font-family:"Prata",serif;color:var(--teal-dark);font-weight:400;text-transform:uppercase;white-space:nowrap}
.card{position:absolute;top:907px;width:223px;height:400px;border-radius:112px;background:var(--mint);text-align:center}
.card .photo{position:absolute;left:17px;top:21px;width:189px;height:189px;border-radius:50%;background:linear-gradient(160deg,#9aa39a,#565f5a)}
.card h3{position:absolute;top:225px;width:100%;font-family:"Prata",serif;font-weight:400;font-size:16px;color:var(--teal-dark)}
.card p{position:absolute;top:260px;left:18px;right:18px;font-size:11.5px;line-height:19px;color:var(--muted)}
.card.featured{background:var(--teal-dark)}
.card.featured h3,.card.featured p{color:#fff}

/* offer */
.offer-title{left:106px;top:1608px;font-size:36px;color:#fff;line-height:46px}
.feature{position:absolute;top:1840px;width:260px;text-align:center;color:#fff}
.feature .ic{width:87px;height:87px;margin:0 auto;border-radius:50%;background:#fff;border-bottom:5px solid var(--teal-dark);display:flex;align-items:center;justify-content:center}
.feature h4{font-family:"Prata",serif;font-weight:400;font-size:16px;margin-top:24px}
.feature p{font-size:12px;margin-top:14px;line-height:20px}

/* services */
.svc-label{position:absolute;font-family:"Prata",serif;font-size:18px;color:var(--ink)}
.svc-icon{position:absolute;width:70px;height:70px;border-radius:50%;border:2px solid var(--teal-dark);display:flex;align-items:center;justify-content:center;background:#fff}
.svc-icon span{width:54px;height:54px;border-radius:50%;border:2px solid var(--green);display:flex;align-items:center;justify-content:center}

/* reviews */
.review{position:absolute;padding:40px 24px 0;text-align:center;font-size:11.5px;line-height:19px;color:#fff}
.review .src{position:absolute;right:18px;top:14px;font-weight:600;font-size:12px;color:#fff}
.review.main{background:#fff;color:var(--muted);box-shadow:0 6px 20px rgba(0,0,0,.15)}
.review.main .src{color:var(--ink)}
.review.side{background:rgba(255,255,255,.1)}
.quote{font-family:"Prata",serif;font-size:64px;line-height:40px;color:rgba(255,255,255,.45);position:absolute;left:0;right:0;top:14px}
.review.main .quote{color:#d8e3d8}
.reviewer{position:absolute;width:200px;text-align:center;color:#fff;font-family:"Prata",serif;font-size:18px}
.reviewer i{display:block;margin:0 auto 6px;width:54px;height:54px;border-radius:50%;background:linear-gradient(#557060,#2c3a33);border:2px solid #fff}

/* experience */
.exp p{position:absolute;left:61px;width:410px;font-size:11.5px;line-height:19px;color:var(--muted)}

/* footer */
.field{position:absolute;left:431px;width:315px;height:36px;border:1px solid #fff;border-radius:4px;color:#fff;font-size:12px;padding:9px 10px}
.hours{position:absolute;left:802px;top:4158px;color:#fff;font-size:12px;line-height:30px}
.hours h4{font-family:"Prata",serif;font-weight:400;font-size:17px;margin-bottom:4px}
.legal{position:absolute;left:0;top:4465px;width:1200px;height:26px;background:var(--green);color:#fff;font-size:11px;display:flex;align-items:center;justify-content:center}
</style>
</head>
<body>

<!-- HERO -->
<section class="hero" role="img" aria-label="Smiling patient in a dental chair giving a thumbs up, with a smiling woman behind him"></section>
<svg class="abs" style="left:0;top:420px" width="1200" height="360" viewBox="0 0 1200 360">
  <path d="M0 60 C 250 290, 650 400, 1200 140 L1200 360 L0 360 Z" fill="#fff"/>
  <path d="M0 60 C 250 290, 650 400, 1200 140" fill="none" stroke="#2d6664" stroke-width="9"/>
</svg>
<div class="topbar">
  <span>Contact Us</span><span>Blog</span><span>Testimonials</span>
  <span class="phone">
    <svg width="32" height="32" viewBox="0 0 32 32"><circle cx="16" cy="16" r="16" fill="#fff"/><path d="M11 9c1-1 2-1 3 0l2 3c.5 1 0 2-1 2.5 1 2 2.5 3.5 4.5 4.5.5-1 1.5-1.5 2.5-1l3 2c1 1 1 2 0 3-2 2-5 2-9-2s-7-9-5-12z" fill="#2d6664"/></svg>
    <span>Maplewood:<br><b>(555) 014-2287</b></span>
  </span>
</div>
<div class="brand" style="left:60px;top:64px">Bright Harbor</div>
<nav class="nav"><span class="active">Home</span><span>About Our Office</span><span>Services</span><span>Financing</span><span>New Patient Visit</span></nav>
<div class="btn" style="left:745px;top:69px;width:127px;height:36px;background:var(--green);color:#fff">Emergency</div>
<div class="btn" style="left:887px;top:69px;width:253px;height:36px">Requaste an Appointment</div>
<div class="script hero-kicker">Gentle</div>
<h1 class="hero-title">CREATING HEALTHIER<br>SMILES</h1>
<div class="hero-lead">With Advanced Technology and Affordable Treatment</div>
<div class="btn" style="left:61px;top:433px;width:235px;height:36px">Book an Appointment</div>

<!-- TEAM -->
<div class="abs eyebrow" style="left:115px;top:792px">Specialist</div>
<h2 class="abs heading" style="left:118px;top:830px;font-size:36px">Meet Our Team</h2>

<div class="card" style="left:117px"><div class="photo" role="img" aria-label="Portrait of Dr. Nisha Rao"></div><h3>Dr. Nisha Rao</h3><p>Dr. Nisha Rao is a graduate of the School of Dental Medicine at Northfield University, Denver.</p></div>
<div class="card featured" style="left:363px"><div class="photo" role="img" aria-label="Portrait of Dr. Priya Menon"></div><h3>Dr. Priya Menon</h3><p>Dr. Menon received her specialty training in Endodontics from Westbrook University. She graduated with a Master</p>
  <svg class="abs" style="left:97px;top:385px" width="30" height="30"><circle cx="15" cy="15" r="15" fill="#5ec6c4"/><path d="M12 9l6 6-6 6" stroke="#fff" stroke-width="2.5" fill="none"/></svg></div>
<div class="card" style="left:610px"><div class="photo" role="img" aria-label="Portrait of Dr. Arun Desai"></div><h3>Dr. Arun Desai</h3><p>Dr. Arun Desai, DDS received his Bachelor of Dental Surgery Degree in 1999 from India. In 2000, he immigrated</p></div>
<div class="card" style="left:858px"><div class="photo" role="img" aria-label="Portrait of Dr. Nisha Rao"></div><h3>Dr. Nisha Rao</h3><p>Dr. Nisha Rao is a graduate of the School of Dental Medicine at Northfield University, Denver.</p></div>

<svg class="abs" style="left:1078px;top:1368px" width="28" height="28"><circle cx="14" cy="14" r="12" fill="none" stroke="#5ec6c4" stroke-width="2"/></svg>

<!-- OFFER BAND -->
<svg class="abs" style="left:0;top:1420px" width="1200" height="680" viewBox="0 0 1200 680">
  <path d="M0 110 C 300 40, 800 0, 1200 20 L1200 660 C 900 620, 400 630, 0 640 Z" fill="#6b9d6c"/>
</svg>
<div class="abs" style="left:767px;top:1395px;width:375px;height:375px;border-radius:48% 52% 45% 55% / 55% 45% 55% 45%;background:linear-gradient(140deg,#dfe7ea,#8fa7b2 60%,#c8b2a6)" role="img" aria-label="Dentist and assistant showing an X-ray to a smiling patient"></div>
<div class="abs" style="left:752px;top:1478px;width:36px;height:48px;border-radius:50%;background:#fff"></div>
<div class="abs script" style="left:106px;top:1568px;color:#a9d3a1;font-size:20px">Committed to excellence in Oral Health Care</div>
<h2 class="abs serif offer-title" style="font-weight:400">FREE EXAM &amp; X-RAY FOR<br>NEW PATIENTS</h2>
<div class="btn" style="left:106px;top:1706px;width:237px;height:35px">Book an Appointment</div>

<div class="feature" style="left:198px"><div class="ic"><svg width="48" height="48" viewBox="0 0 48 48" fill="none" stroke="#2d6664" stroke-width="2"><rect x="8" y="26" width="32" height="14" rx="2"/><path d="M18 26v-8h12v8M24 10v8M14 40v-6M34 40v-6"/></svg></div><h4>Dental Implants</h4><p>Affordable for our patients.</p></div>
<div class="feature" style="left:467px"><div class="ic"><svg width="48" height="48" viewBox="0 0 48 48" fill="none" stroke="#2d6664" stroke-width="2"><path d="M24 40S8 30 8 18a8 8 0 0 1 16-2 8 8 0 0 1 16 2c0 12-16 22-16 22z"/><circle cx="30" cy="30" r="7"/><path d="M25 35l10-10"/></svg></div><h4>No Insurance</h4><p>Check out our SmileCredit Program.</p></div>
<div class="feature" style="left:751px"><div class="ic"><svg width="48" height="48" viewBox="0 0 48 48" fill="none" stroke="#2d6664" stroke-width="2"><rect x="6" y="16" width="26" height="18"/><path d="M32 22h6l4 6v6H32M19 20v10M14 25h10"/><circle cx="14" cy="36" r="3"/><circle cx="36" cy="36" r="3"/></svg></div><h4>Emergency</h4><p>Available Evenings, Weekends and<br>for Emergencies.</p></div>

<!-- SERVICES -->
<div class="abs eyebrow" style="left:0;width:1200px;text-align:center;top:2188px">We Provide</div>
<h2 class="abs heading" style="left:0;width:1200px;text-align:center;top:2226px;font-size:36px">Our Services</h2>

<div class="svc-label" style="left:0;width:1200px;text-align:center;top:2286px">Braces</div>
<div class="svc-icon" style="left:565px;top:2314px"><span><svg width="30" height="20"><rect x="2" y="4" width="26" height="12" rx="6" fill="none" stroke="#2d6664" stroke-width="2"/></svg></span></div>

<div class="svc-label" style="left:148px;top:2435px">Cosmetic Dentistry</div>
<div class="svc-icon" style="left:343px;top:2417px"><span><svg width="28" height="22"><rect x="2" y="3" width="24" height="16" rx="3" fill="none" stroke="#2d6664" stroke-width="2"/><path d="M2 11h24M10 3v16M18 3v16" stroke="#2d6664" stroke-width="1.5"/></svg></span></div>

<div class="svc-icon" style="left:790px;top:2417px"><span><svg width="26" height="28"><path d="M4 6c4-4 14-4 18 0 2 6-2 20-4 20s-2-8-5-8-3 8-5 8S2 12 4 6z" fill="none" stroke="#2d6664" stroke-width="2"/></svg></span></div>
<div class="svc-label" style="left:879px;top:2435px">Gum Disease</div>

<div class="svc-label" style="left:140px;top:2619px">Dental Implants</div>
<div class="svc-icon" style="left:317px;top:2597px"><span><svg width="26" height="28"><path d="M5 4h16v8H5zM13 12v14M9 16h8M9 20h8" fill="none" stroke="#2d6664" stroke-width="2"/></svg></span></div>

<div class="svc-icon" style="left:811px;top:2597px"><span><svg width="26" height="28"><path d="M4 6c4-4 14-4 18 0 2 6-2 20-4 20s-2-8-5-8-3 8-5 8S2 12 4 6z" fill="none" stroke="#2d6664" stroke-width="2"/><path d="M11 8v8M15 8v8" stroke="#2d6664" stroke-width="1.5"/></svg></span></div>
<div class="svc-label" style="left:901px;top:2619px">Root Canal</div>

<svg class="abs" style="left:460px;top:2414px" width="276" height="276" viewBox="0 0 276 276">
  <circle cx="138" cy="138" r="132" fill="none" stroke="#eef4ee" stroke-width="3"/>
  <circle cx="138" cy="138" r="100" fill="none" stroke="#eef4ee" stroke-width="14"/>
  <circle cx="138" cy="138" r="86" fill="#fff"/>
  <g fill="#6b9d6c"><circle cx="138" cy="6" r="5"/><circle cx="39" cy="48" r="5"/><circle cx="237" cy="48" r="5"/><circle cx="28" cy="210" r="5"/><circle cx="248" cy="207" r="5"/></g>
</svg>
<div class="brand" style="left:510px;top:2533px;width:180px;text-align:center;font-size:24px">Bright Harbor</div>
<svg class="abs" style="left:578px;top:2690px" width="44" height="16"><circle cx="8" cy="8" r="3" fill="#2d6664"/><circle cx="22" cy="8" r="6" fill="none" stroke="#2d6664"/><circle cx="22" cy="8" r="3" fill="#2d6664"/><circle cx="36" cy="8" r="3" fill="#2d6664"/></svg>

<!-- REVIEWS -->
<svg class="abs" style="left:0;top:2760px" width="1200" height="700" viewBox="0 0 1200 700">
  <path d="M0 80 C 400 20, 800 10, 1200 30 L1200 680 C 800 700, 400 660, 0 640 Z" fill="#6b9d6c"/>
</svg>
<div class="abs script" style="left:0;width:1200px;text-align:center;top:2842px;color:#a9d3a1;font-size:22px">Reviews</div>
<h2 class="abs serif" style="left:0;width:1200px;text-align:center;top:2880px;font-size:32px;font-weight:400;color:#fff">OUR PATIENTS SAY ?</h2>
<div class="abs serif" style="left:0;width:1200px;text-align:center;top:2935px;font-size:19px;color:#fff">Average Rating</div>
<div class="abs" style="left:442px;top:2969px;color:#f4c542;font-size:17px;letter-spacing:2px">★★★★★ <span style="color:#fff;font-size:16px;letter-spacing:0">4.9</span></div>
<div class="abs" style="left:620px;top:2972px;color:#fff;font-size:14px;display:flex;align-items:center;gap:10px"><i style="display:inline-block;width:24px;height:14px;border-radius:7px;background:#3a7bd5"></i>126 Reviews</div>
<div class="abs" style="left:398px;top:3012px;display:flex;gap:36px;align-items:center;color:#fff;font-weight:600;font-size:19px">
  <span>SearchStar</span><span>LocalPicks</span><span style="background:#3b5a9a;padding:4px 10px;border-radius:3px">FriendSpace</span>
</div>

<div class="review side" style="left:78px;top:3130px;width:353px;height:184px"><span class="src">LocalPicks</span><div class="quote">“</div>As most of us know going to the dentist isn't our favorite thing. But at this dental office the entire staff is super friendly, efficient, and professional. They</div>
<div class="review side" style="left:762px;top:3130px;width:353px;height:184px"><span class="src">LocalPicks</span><div class="quote">“</div>Went here last July 2021 for the removal of my impacted wisdom tooth. Office is clean, staff are courteous. Massage chair. Wait was quick. I chose the laughing</div>
<div class="review main" style="left:424px;top:3089px;width:352px;height:186px"><span class="src">LocalPicks</span><div class="quote">“</div>I am so happy I found Bright Harbor in Maplewood. This is a long over due review since I have been seeing them for almost two years. They are always so friendly, understanding and empathetic when they have to deliver</div>

<div class="reviewer" style="left:155px;top:3292px"><i role="img" aria-label="Reviewer avatar"></i>Owen K.</div>
<div class="reviewer" style="left:500px;top:3246px"><i role="img" aria-label="Reviewer avatar"></i>Leena M.</div>
<div class="reviewer" style="left:838px;top:3292px"><i role="img" aria-label="Reviewer avatar"></i>Dario F.</div>

<!-- EXPERIENCE -->
<section class="exp">
  <div class="abs eyebrow" style="left:61px;top:3538px">Specialist</div>
  <h2 class="abs heading" style="left:61px;top:3580px;font-size:36px;line-height:52px">Experience the Bright<br>Harbor Difference</h2>
  <p style="top:3690px">At Bright Harbor, we provide affordable and expert dental solutions. Whether you are looking for a family dentist or have any emergency such as needing a root canal in Maplewood, we are here for you! We want to keep your teeth healthy inside and out. We don't just clean teeth and send you on your way, we want to get to know you.</p>
  <p style="top:3818px">We accept most HMO and PPO insurances. We offer various financing options through SmileCredit, LendWell and In-House Plans.</p>
  <div class="btn" style="left:61px;top:3906px;width:253px;height:34px">Requaste an Appointment</div>
  <div class="abs" style="left:684px;top:3538px;width:458px;height:440px;border-radius:50%;background:#eef4ee"></div>
  <div class="abs" style="left:700px;top:3540px;width:442px;height:430px;border-radius:48% 52% 50% 50%;background:linear-gradient(150deg,#c9d7dc,#e9cbb6 55%,#b98a63)" role="img" aria-label="Smiling young woman in a dental chair with a dental mirror"></div>
</section>

<!-- FOOTER -->
<svg class="abs" style="left:0;top:4000px" width="1200" height="470" viewBox="0 0 1200 470">
  <defs><linearGradient id="ft" x1="0" x2="1"><stop offset="0" stop-color="#234847"/><stop offset="1" stop-color="#1a3332"/></linearGradient></defs>
  <path d="M0 160 C 300 30, 800 10, 1200 40 L1200 470 L0 470 Z" fill="url(#ft)"/>
</svg>
<div class="brand" style="left:300px;top:4070px">Bright Harbor</div>
<div class="abs" style="left:61px;top:4158px;width:314px;height:220px;background:linear-gradient(135deg,#eef0ec,#dde4e6)" role="img" aria-label="Street map showing the office location"></div>
<div class="abs" style="left:70px;top:4168px;width:200px;height:66px;background:#fff;padding:8px 10px 0 40px;font-size:10.5px;line-height:18px;color:#555">48 Harbor View Rd.,<br>Suite B<br>Maplewood, ST 00000
  <svg class="abs" style="left:10px;top:10px" width="18" height="24"><path d="M9 0a8 8 0 0 1 8 8c0 6-8 16-8 16S1 14 1 8a8 8 0 0 1 8-8z" fill="#2d6664"/><circle cx="9" cy="8" r="3" fill="#fff"/></svg></div>
<div class="field" style="top:4160px">Name *</div>
<div class="field" style="top:4208px">Address *</div>
<div class="field" style="top:4257px">Phone *</div>
<div class="btn" style="left:431px;top:4311px;width:210px;height:36px">Free Consultation</div>
<div class="hours"><h4>Dental Implants</h4>Monday 10AM–7PM<br>Tuesday 10AM–7PM<br>Wednesday 9AM–6PM<br>Thursday 9AM–6PM<br>Friday 9AM–5PM<br>Saturday 9AM–1PM</div>
<div class="legal">All rights reserved. mybrightharbor.example</div>

</body>
</html>
```